Coastline Premier Retreats Business Card Design

Design a business card for Coastline Premier Retreats. Look at the website for colors and reference. Card should have logo, name, title, office number, mobile number, email, URL and a tagline like, "Luxury Hotel & Resort Email Marketing" (This might change).

https://www.coastlinepremierretreats.example

The rest I will leave up to your imagination.

Contact Information for Business Card

Logo, name, title, office number, mobile number, email, URL and a tagline like, "Luxury Hotel & Resort Email Marketing" (This might change).

```html
<!DOCTYPE html>
<html lang="en">
<head>
<meta charset="utf-8">
<title>Coastline Premier Retreats – Business Card</title>
<link href="https://fonts.googleapis.com/css2?family=Exo+2:wght@400;500;700;800&display=swap" rel="stylesheet">
<style>
  :root {
    --backdrop: #1f1f1f;
    --card-black: #121212;
    --card-white: #ffffff;
    --accent: #f47100;
    --text-light: #ffffff;
    --text-dark: #111111;
    --logo-grey: #3a3a3a;
  }
  * { box-sizing: border-box; margin: 0; padding: 0; }
  html, body {
    width: 1200px; height: 1015px; overflow: hidden;
    background: var(--backdrop);
    font-family: "Exo 2", sans-serif;
  }
  .card {
    position: absolute;
    width: 560px; height: 320px;
    overflow: hidden;
    box-shadow: 0 14px 30px rgba(0,0,0,.55);
  }

  /* ---------- Card back ---------- */
  .card-back { left: 90px; top: 110px; background: var(--card-black); }
  .card-back .brand {
    position: absolute; left: 0; right: 0; top: 92px;
    display: flex; align-items: center; justify-content: center; gap: 14px;
  }
  .card-back .brand-square { width: 18px; height: 18px; background: var(--logo-grey); }
  .card-back .brand-name {
    font-weight: 800; font-size: 27px; letter-spacing: 2px;
    text-transform: uppercase; color: var(--logo-grey);
  }
  .card-back .tagline-band {
    position: absolute; left: 0; right: 0; top: 228px; height: 36px;
    background: var(--accent);
    display: flex; align-items: center; justify-content: center;
  }
  .card-back .tagline {
    color: var(--text-light); font-weight: 800; font-size: 15px;
    letter-spacing: 1.6px; text-transform: uppercase;
  }

  /* ---------- Card front ---------- */
  .card-front { left: 550px; top: 560px; background: var(--card-black); }
  .card-front .top-panel {
    position: absolute; left: 0; right: 0; top: 0; height: 168px;
    background: var(--card-white);
    border-bottom: 4px solid var(--accent);
    display: flex; align-items: center; justify-content: center; gap: 12px;
  }
  .card-front .brand-square { width: 16px; height: 16px; background: var(--accent); }
  .card-front .brand-name {
    font-weight: 800; font-size: 25px; letter-spacing: 1.6px;
    text-transform: uppercase; color: var(--text-dark);
  }
  .card-front .person {
    position: absolute; left: 0; right: 0; top: 190px; text-align: center;
    color: var(--text-light);
  }
  .card-front .person-name {
    font-weight: 800; font-size: 19px; letter-spacing: 2px; text-transform: uppercase;
  }
  .card-front .person-title { font-size: 13px; margin-top: 2px; }
  .card-front .contacts {
    position: absolute; left: 0; right: 0; top: 252px;
    display: flex; justify-content: center; align-items: stretch; gap: 18px;
    color: var(--text-light); font-size: 12.5px;
  }
  .card-front .contact-col { display: flex; flex-direction: column; gap: 6px; }
  .card-front .contact-col.online { align-items: flex-end; }
  .card-front .contact-item { display: flex; align-items: center; gap: 7px; }
  .card-front .divider { width: 1px; background: #9a9a9a; }
  .icon { width: 14px; height: 14px; flex: none; }
  .icon * { fill: none; stroke: var(--accent); stroke-width: 1.6; stroke-linecap: round; stroke-linejoin: round; }
</style>
</head>
<body>

<section class="card card-back" aria-label="Business card back">
  <div class="brand">
    <span class="brand-square"></span>
    <span class="brand-name">Coastline Premier Retreats</span>
  </div>
  <div class="tagline-band">
    <p class="tagline">Luxury Hotel &amp; Resort Email Marketing</p>
  </div>
</section>

<section class="card card-front" aria-label="Business card front">
  <div class="top-panel">
    <span class="brand-square"></span>
    <span class="brand-name">Coastline Premier Retreats</span>
  </div>

  <div class="person">
    <p class="person-name">Marcus Ellison</p>
    <p class="person-title">Managing Director</p>
  </div>

  <div class="contacts">
    <div class="contact-col online">
      <p class="contact-item">info@coastlinepremierretreats.example
        <svg class="icon" viewBox="0 0 16 16"><rect x="1.5" y="3.5" width="13" height="9"/><path d="M1.5 3.5 8 9l6.5-5.5"/></svg>
      </p>
      <p class="contact-item">coastlinepremierretreats.example
        <svg class="icon" viewBox="0 0 16 16"><circle cx="8" cy="8" r="6.5"/><path d="M1.5 8h13M8 1.5c-3 3.5-3 9.5 0 13M8 1.5c3 3.5 3 9.5 0 13"/></svg>
      </p>
    </div>
    <span class="divider"></span>
    <div class="contact-col">
      <p class="contact-item">
        <svg class="icon" viewBox="0 0 16 16"><path d="M4 1.8 6.2 4.5 5 6.3c.9 1.8 2.5 3.4 4.3 4.3l1.8-1.2 2.7 2.2-1.3 2C7.5 13.6 2.4 8.5 2 3.1z"/></svg>
        044-555 018 274
      </p>
      <p class="contact-item">
        <svg class="icon" viewBox="0 0 16 16"><rect x="4" y="1.5" width="8" height="13" rx="1.5"/><path d="M7 12.2h2"/></svg>
        044-555 018 274
      </p>
    </div>
  </div>
</section>

</body>
</html>
```